US Recruiting Firm Needs Dynamic Tri-Fold Brochure

Need tri-fold professional brochure for HR recruiting and consulting firm based in the US.

Target Market(s)

Clients seeking administrative and human resources talent

Industry/Entity Type

Recruitment

Font styles to use
Sans Serif

Requirements
Should not have
• No weird shapes
• No heavy geometric shapes -- I prefer curvy lines
• Not a dark brochure

```html
<!DOCTYPE html>
<html lang="en">
<head>
<meta charset="utf-8">
<title>Harborline Office Recruiters – Tri-Fold Brochure</title>
<link href="https://fonts.googleapis.com/css2?family=Didact+Gothic&family=Montserrat:wght@600;700&display=swap" rel="stylesheet">
<style>
:root{
  --navy:#14365c;
  --navy-deep:#0e2a4a;
  --orange:#e8730f;
  --orange-deep:#c9560a;
  --lime:#9ccc2f;
  --purple:#8a2a8c;
  --ink:#2d3440;
  --paper:#ffffff;
  --mist:#eef1f4;
  --backdrop:#e4e6e9;
}
*{box-sizing:border-box;margin:0;padding:0}
html,body{width:798px;height:1200px;overflow:hidden;background:var(--backdrop)}
body{font-family:"Didact Gothic",sans-serif;color:var(--ink)}
.canvas{position:relative;width:798px;height:1200px}
.spread{position:absolute;left:29px;width:740px;height:572px;background:var(--paper);box-shadow:0 4px 14px rgba(0,0,0,.18);overflow:hidden}
.spread--outside{top:20px}
.spread--inside{top:608px}
.panel{position:absolute;top:0;width:246.67px;height:572px}
.panel--1{left:0}
.panel--2{left:246.67px;border-left:1px solid #e2e5e9}
.panel--3{left:493.33px;border-left:1px solid #e2e5e9}
.photo{position:absolute;left:0;width:100%}
.edge{position:absolute;left:0;bottom:0;width:100%;height:16px;background:var(--lime)}
.web{position:absolute;left:0;bottom:16px;width:100%;height:34px;border-top:1.5px solid var(--purple);display:flex;align-items:center;justify-content:center;font-family:"Montserrat",sans-serif;font-weight:600;font-size:12px;color:var(--navy);background:var(--paper)}
/* outside */
.about-banner{position:absolute;top:34px;left:26px;width:190px;height:30px;background:var(--navy);color:#fff;font-family:"Montserrat",sans-serif;font-weight:700;font-size:14px;display:flex;align-items:center;justify-content:center;letter-spacing:.5px;border-radius:0 12px 0 12px}
.about-copy{position:absolute;top:84px;left:22px;right:20px;font-size:9.6px;line-height:1.5}
.about-copy p+p{margin-top:10px}
.cta{position:absolute;left:0;top:262px;width:100%;height:160px;background:linear-gradient(135deg,var(--orange),var(--orange-deep));color:#fff;padding:20px 20px}
.cta__lead{font-family:"Montserrat",sans-serif;font-weight:700;font-size:17px;line-height:1.15}
.cta__sub{font-size:10.5px;line-height:1.35;margin-top:4px}
.cta__sub strong{font-family:"Montserrat",sans-serif;font-weight:700;font-size:12px;display:block}
.cta__call{font-family:"Montserrat",sans-serif;font-weight:700;font-size:15px;margin-top:8px}
.cta__mail{font-size:10.5px;margin-top:3px}
.outside-web{position:absolute;left:0;bottom:16px;width:100%;height:120px;display:flex;align-items:flex-end;justify-content:center;padding-bottom:20px;font-family:"Montserrat",sans-serif;font-weight:600;font-size:12.5px;color:var(--navy)}
.brand{position:absolute;top:12px;left:16px;right:12px;display:flex;align-items:center;gap:8px}
.brand__dot{width:26px;height:26px;border-radius:50%;background:var(--purple);flex:none}
.brand__name{font-family:"Montserrat",sans-serif;font-weight:700;font-size:12px;line-height:1.15;color:var(--navy)}
.brand__tag{font-size:8.5px;color:var(--ink);margin-top:2px}
.cover-band{position:absolute;left:0;top:392px;width:100%;height:164px;background:linear-gradient(160deg,var(--navy),var(--navy-deep));display:flex;align-items:center;justify-content:center;text-align:center}
.cover-band h2{font-family:"Montserrat",sans-serif;font-weight:600;font-size:17px;line-height:1.3;color:var(--orange);letter-spacing:.3px}
/* inside */
.heading{font-family:"Montserrat",sans-serif;font-weight:700;color:var(--navy);font-size:13px;line-height:1.2;padding-bottom:5px;border-bottom:1.5px solid var(--purple);display:inline-block}
.block{position:absolute;left:20px;right:18px}
.body-copy{font-size:9.4px;line-height:1.5;margin-top:8px}
.ticks{list-style:none;margin-top:8px}
.ticks li{position:relative;padding-left:16px;font-size:9.6px;line-height:1.55}
.ticks li::before{content:"";position:absolute;left:2px;top:2px;width:4px;height:8px;border-right:2px solid var(--orange);border-bottom:2px solid var(--orange);transform:rotate(40deg)}
.ticks--tight li{font-size:9.2px;line-height:1.48}
.positions{position:absolute;left:246.67px;top:322px;width:493.33px;height:200px;background:linear-gradient(160deg,var(--navy),var(--navy-deep));color:#fff;padding:16px 20px 0}
.positions h3{font-family:"Montserrat",sans-serif;font-weight:700;font-size:12px;line-height:1.3;letter-spacing:.2px}
.positions__cols{display:flex;gap:40px;margin-top:6px}
.positions__cols .ticks{margin-top:0;width:200px}
.positions__cols .ticks li{font-size:9px;line-height:1.45}
.inside-web{position:absolute;bottom:16px;height:34px;border-top:1.5px solid var(--purple);display:flex;align-items:center;justify-content:center;font-family:"Montserrat",sans-serif;font-weight:600;font-size:12px;color:var(--navy);background:var(--paper)}
</style>
</head>
<body>
<main class="canvas">

  <section class="spread spread--outside" aria-label="Brochure outside">
    <div class="panel panel--1">
      <div class="about-banner">ABOUT US</div>
      <div class="about-copy">
        <p>Harborline Office Recruiters is a recruiting and search firm that specializes in providing top-notch administrative and human resources talent. We provide best-in-class talent to companies seeking to attract and retain the best employees, simplify their recruiting process, increase efficiency, and optimize productivity.</p>
        <p>Each search is customized based on the client's requirements. We provide quality, timely, and efficient services. Our recruiters are highly skilled in identifying, screening, interviewing, and assessing candidates across various industries. We develop a partnership with our client and candidate in order to make the recruitment process a success for both parties.</p>
      </div>
      <div class="photo" style="top:360px;height:196px;background:linear-gradient(160deg,#c9d2dc,#8d7b6a 55%,#3b3f4a)" role="img" aria-label="Photo of a smiling business team gathered around a laptop at a meeting table"></div>
      <div class="edge"></div>
    </div>

    <div class="panel panel--2">
      <div class="photo" style="top:0;height:262px;background:linear-gradient(180deg,#eef2f6,#c3ccd6 60%,#6f7884)" role="img" aria-label="Photo of professionals shaking hands in a bright glass-walled office"></div>
      <div class="cta">
        <div class="cta__lead">TO LEARN MORE</div>
        <div class="cta__sub">AND REQUEST A<strong>FREE CONSULTATION</strong>CONTACT US TODAY</div>
        <div class="cta__call">CALL - 555 014 2290</div>
        <div class="cta__mail">hello@harborlineoffice.com</div>
      </div>
      <div class="outside-web">www.harborlineoffice.com</div>
      <div class="edge"></div>
    </div>

    <div class="panel panel--3">
      <div class="brand">
        <span class="brand__dot"></span>
        <div>
          <div class="brand__name">HARBORLINE OFFICE<br>RECRUITERS</div>
          <div class="brand__tag">Human Resources Staffing &amp; Consulting</div>
        </div>
      </div>
      <div class="photo" style="top:62px;height:330px;background:linear-gradient(160deg,#e9ecef,#9c8a7c 50%,#4b4f5c)" role="img" aria-label="Photo of a confident professional woman in glasses with colleagues behind her"></div>
      <div class="cover-band"><h2>SPECIALIZING IN<br>ADMINISTRATIVE<br>&amp; HR TALENT</h2></div>
      <div class="edge"></div>
    </div>
  </section>

  <section class="spread spread--inside" aria-label="Brochure inside">
    <div class="panel panel--1">
      <div class="block" style="top:22px">
        <h2 class="heading">A TRUSTED<br>RECRUITING PARTNER</h2>
        <p class="body-copy">We have over 20 years of recruiting and human resources experience. Our recruiters have the expertise, insights, and passion to bring value-added recruiting services to your company. We have a track record of excellence.</p>
      </div>
      <div class="block" style="top:160px">
        <h2 class="heading">WHY CHOOSE US?</h2>
        <ul class="ticks">
          <li>Dedicated to admin &amp; HR recruiting</li>
          <li>Highly qualified talent network</li>
          <li>Comprehensive pre-screening</li>
          <li>Simplified recruiting process</li>
          <li>Reasonable placement fees</li>
          <li>90-day replacement guarantee</li>
        </ul>
      </div>
      <div class="photo" style="top:330px;height:192px;background:linear-gradient(160deg,#dfe4ea,#a69585 55%,#3f434e)" role="img" aria-label="Photo of a presenter leading a training session for seated professionals"></div>
      <div class="web">www.harborlineoffice.com</div>
      <div class="edge"></div>
    </div>

    <div class="panel panel--2">
      <div class="block" style="top:22px">
        <h2 class="heading">OUR MISSION</h2>
        <p class="body-copy">We have a two-fold mission. We help companies hire the best administrative and human resources staff to help meet organizational goals and cultivate a highly engaged, productive workforce. We also help job seekers find fulfilling employment with awesome companies.</p>
      </div>
      <div class="photo" style="top:140px;height:182px;background:linear-gradient(160deg,#e6eaee,#9a8f86 55%,#3c414c)" role="img" aria-label="Photo of business people shaking hands across a meeting table"></div>
    </div>

    <div class="panel panel--3">
      <div class="block" style="top:22px">
        <h2 class="heading">WE PROVIDE CUSTOMIZED<br>RECRUITING AND CONSULTING<br>SERVICES.</h2>
        <ul class="ticks ticks--tight">
          <li>Requisition management</li>
          <li>Position &amp; candidate profiling</li>
          <li>Sourcing resumes</li>
          <li>Writing and placing job postings</li>
          <li>Screening &amp; interviewing candidates</li>
          <li>Shortlisting candidates</li>
          <li>Candidate assessment</li>
          <li>Coordinating interviews &amp; debriefing</li>
          <li>Candidate dispositioning &amp; updates</li>
          <li>Applicant tracking</li>
          <li>Job offer &amp; salary negotiation</li>
          <li>Offer letter &amp; new hire paperwork</li>
          <li>Due Diligence</li>
          <li>New hire check-in surveys</li>
        </ul>
      </div>
    </div>

    <div class="positions">
      <h3>WE OFFER STELLAR ADMINISTRATIVE AND HR TALENT. POSITIONS<br>THAT WE FILL INCLUDE:</h3>
      <div class="positions__cols">
        <ul class="ticks">
          <li>HR Assistant</li>
          <li>HR Coordinator</li>
          <li>Recruiting Coordinator</li>
          <li>HR Specialist</li>
          <li>HR Generalist</li>
          <li>HR Consultant</li>
          <li>HR Manager</li>
          <li>HR Director</li>
          <li>Employee Relations</li>
        </ul>
        <ul class="ticks">
          <li>Talent Acquisition Consultant</li>
          <li>Recruiter</li>
          <li>Benefits Specialist</li>
          <li>Compensation Specialist</li>
          <li>Training Specialist</li>
          <li>Learning &amp; Development Consultant</li>
          <li>Diversity &amp; Inclusion Consultant</li>
          <li>Administrative Assistant</li>
          <li>Executive Assistant</li>
          <li>Office Manager</li>
        </ul>
      </div>
    </div>

    <div class="inside-web" style="left:246.67px;width:246.67px">www.harborlineoffice.com</div>
    <div class="inside-web" style="left:493.33px;width:246.67px">www.harborlineoffice.com</div>
    <div class="edge" style="left:246.67px;width:493.33px"></div>
  </section>

</main>
</body>
</html>
```